Web Design For Marlow Pool Service

We are working with a company that wants a website for their pool service. Some sites to use for content/competitors and inspiration:
https://sacramento.brightwaterpoolco.example/builder/newbuild/repair/ppc
https://hollowbrookpoolcareplus.example/
https://lakemontpoolservice.example/
https://www.dravenspoolresurfacing.example/pool-renovation-ga/
Thank you for taking the time to consider designing a website for us. We are web developers based in Stockton, CA, USA. Most of our projects go through the same process. Understanding this process may help you win a project with us. We custom-code all of our websites in-house. We don’t have any requirements as to what tools you use for your design, but we prefer Figma files. For any design that we label as four-stars, we send it to the client for review. The client picks the final design they want us to use. Once we complete this process, we will continue to show additional clients all the four-star sites and purchase them later. Your designs will have multiple chances to sell. For better chances of success, we ask that you follow these guidelines.
IMAGES:
If you use any images or icons in the design, we ask that you have a link to the asset so we can purchase the image/icon. Most of the designs we submit do not have the customer’s images on them unless they have some great images. Be creative; show us the feeling you are trying to portray with your image choices. Use any royalty-free site you choose. We subscribe to Adobe and mainly use their images, but we can purchase images outside of Adobe. PLEASE NOTE: we will not submit designs to clients with watermarks on the images.
FONTS:
We ask that you identify the fonts used in the design. This can be done in a message if you want. We typically use Google Fonts and Adobe Fonts.
CONTENT:
We're always open to different content and ideas. We often submit designs with stock images so the client can see our vision. We typically take pictures after the website launch to use their images with our vision. Lorem Ipsum is fine for paragraphs, but we ask that you write the headers in correct English. We want to be able to show the vision and identify the sections of the website.
INSPIRATION:
We typically add a couple of links in the brief of websites we like to help you get started in your design.
REVISIONS:
We do not often ask for revisions of the designs unless we see something in the design that may not appeal to the client. If there are slight changes that we want to make, we do that in the development process.
FEEDBACK:
We rarely give feedback on designs during the design process. We are working on many website projects and do not have the time to provide feedback. We usually respond if your request is well thought out and asks specific questions, but a note asking “feedback, please” usually goes unanswered.
Number of Pages Required
1 page
Look and feel
Each slider illustrates characteristics of the customer's brand and the style your logo design should communicate.

```html
<!DOCTYPE html>
<html lang="en">
<head>
<meta charset="utf-8">
<title>Marlow Pool Service</title>
<link rel="stylesheet" href="https://fonts.googleapis.com/css2?family=Open+Sans:ital,wght@0,400;0,600;0,700;1,400&display=swap">
<style>
:root{
  --navy:#16396a;
  --navy-deep:#0e1631;
  --navy-bar:#272e4c;
  --blue:#2c9cf0;
  --blue-soft:#e3f1fc;
  --ink:#1b2b44;
  --text:#5a5f66;
  --card-text:#4a6c9c;
  --grey-bg:#f5f6f8;
  --star:#c8102e;
  --white:#ffffff;
}
*{box-sizing:border-box;margin:0;padding:0}
html,body{width:1200px;height:5220px;overflow:hidden}
body{font-family:"Open Sans",Arial,sans-serif;color:var(--text);background:var(--white);position:relative}
.abs{position:absolute}
section,header,footer{position:absolute;left:0;width:1200px}

/* header */
.site-header{top:0;height:126px;background:var(--white);z-index:3}
.contact-chip{display:flex;align-items:center;gap:10px;top:20px}
.chip-icon{width:30px;height:30px;border-radius:50%;background:var(--navy);display:flex;align-items:center;justify-content:center}
.chip-text{font-size:11px;line-height:15px;color:var(--ink)}
.chip-text b{display:block;font-size:12px}
.book-btn{top:14px;left:880px;width:182px;height:40px;border-radius:20px;background:var(--navy);color:#fff;font-size:12px;font-weight:600;display:flex;align-items:center;justify-content:center;letter-spacing:.3px}
.header-rule{top:71px;height:1px;background:#dfe3ea}
.main-nav a{position:absolute;top:89px;font-size:12px;color:#4d5660;text-decoration:none}
.logo-tab{top:0;left:503px;width:186px;height:146px;background:#fff;border-radius:0 0 26px 26px;display:flex;align-items:center;justify-content:center;padding-top:22px}
.brand{font-size:14px;font-weight:600;color:var(--navy);letter-spacing:1.4px;text-transform:uppercase;text-align:center;line-height:20px}

/* hero */
.hero{top:126px;height:758px;background:
  radial-gradient(ellipse 520px 300px at 900px 320px,rgba(150,120,95,.55),transparent 70%),
  radial-gradient(ellipse 600px 260px at 180px 560px,rgba(40,90,120,.55),transparent 70%),
  linear-gradient(100deg,#2a2826 0%,#4a423b 45%,#5e5248 65%,#2e2b29 100%)}
.hero-kicker{top:253px;left:107px;font-size:19px;font-weight:600;letter-spacing:5.5px;color:#fff}
.hero-title{top:270px;left:100px;font-size:66px;font-weight:600;color:#fff;letter-spacing:.5px}
.hero-rule{top:360px;left:107px;width:623px;height:2px;background:#4a86d0}
.hero-copy{top:378px;left:107px;width:640px;font-size:16px;line-height:28px;color:#fff}
.btn{display:flex;align-items:center;justify-content:center;border-radius:21px;font-size:14px;font-weight:700;color:#fff;height:40px}
.btn-learn{top:467px;left:107px;width:146px;background:var(--blue)}
.btn-quote{top:467px;left:263px;width:181px;background:#111}

/* feature cards */
.features{top:807px;left:93px;width:1014px;height:280px;display:flex;justify-content:space-between;z-index:2}
.feature{width:318px;height:280px;background:#fff;border-radius:4px;box-shadow:0 4px 18px rgba(0,0,0,.10);text-align:center;padding-top:32px}
.feature-icon{width:62px;height:62px;border-radius:50%;background:var(--blue-soft);margin:0 auto;display:flex;align-items:center;justify-content:center}
.feature h3{margin-top:30px;font-size:17px;font-weight:600;color:var(--navy)}
.feature p{margin:14px auto 0;width:250px;font-size:12.5px;line-height:26px;color:var(--card-text)}

/* shared section headings */
.eyebrow{font-size:11px;font-weight:700;color:var(--blue);letter-spacing:.4px;text-transform:uppercase;display:flex;align-items:center;gap:8px}
.eyebrow::after,.eyebrow.center::before{content:"";width:10px;height:2px;background:var(--blue)}
.centered{left:0;width:1200px;text-align:center;justify-content:center}
.section-title{font-size:34px;font-weight:600;color:var(--navy)}
.section-lead{font-size:13px;line-height:26px;color:var(--text);width:600px;left:300px;text-align:center}

/* about */
.about-title{top:1198px;left:97px;font-size:34px;line-height:53px;font-weight:600;color:var(--navy)}
.about-copy{top:1318px;left:97px;width:420px;font-size:13.4px;line-height:25.4px;color:var(--text)}
.btn-contact{top:1547px;left:97px;width:154px;height:43px;background:var(--navy);border-radius:2px;color:#fff;font-size:15px;font-weight:600;display:flex;align-items:center;justify-content:center;gap:14px}
.about-photo{top:1186px;left:602px;width:498px;height:405px;border-radius:6px;background:linear-gradient(120deg,#1b8fd0 0%,#3ab3e8 35%,#b8bcc0 55%,#8a8f94 70%,#c23b3b 88%,#9e2a2a 100%)}
.about-ring{top:1312px;left:530px;width:124px;height:124px;border-radius:50%;border:1px dashed #9cc8ee}
.about-dot{top:1348px;left:586px;width:52px;height:52px;border-radius:50%;background:#fff;box-shadow:0 2px 10px rgba(0,0,0,.15);display:flex;align-items:center;justify-content:center}

/* services */
.services{top:1687px;height:634px;background:var(--grey-bg)}
.service-row{top:241px;left:91px;width:1014px;display:flex;justify-content:space-between}
.service{position:relative;width:320px;height:310px}
.service-photo{width:320px;height:283px;border-radius:4px}
.service-label{position:absolute;left:35px;top:259px;width:250px;height:51px;background:#fff;border-radius:3px;box-shadow:0 4px 14px rgba(0,0,0,.10);display:flex;align-items:center;justify-content:center;font-size:18px;font-weight:600;color:var(--navy)}

/* call band */
.call-band{top:2321px;height:308px;background:linear-gradient(180deg,#1f2123 0%,#2f3337 60%,#3a3f44 100%)}
.call-title{top:108px;font-size:32px;line-height:40px;font-weight:600;color:#fff}
.call-title span{color:var(--blue)}
.call-bar{top:2597px;left:351px;width:500px;height:52px;background:#fff;box-shadow:0 6px 18px rgba(0,0,0,.12);border-radius:3px;display:flex;align-items:center;font-size:15px;color:#111;z-index:2}

/* testimonials */
.testimonials{top:2629px;height:671px;background:#fff}
.review-row{top:270px;left:91px;width:1016px;display:flex;justify-content:space-between}
.review{width:320px;position:relative;text-align:center}
.review-card{height:263px;background:#fff;box-shadow:0 4px 18px rgba(0,0,0,.08);padding-top:64px}
.avatar{position:absolute;left:127px;top:-31px;width:66px;height:66px;border-radius:50%;background:linear-gradient(160deg,#6d7b88,#2f3a45);border:3px solid #fff;box-shadow:0 2px 8px rgba(0,0,0,.2)}
.stars{font-size:19px;letter-spacing:8px;color:var(--star)}
.review-card p{margin:14px auto 0;width:230px;font-size:13px;line-height:24px;color:#7b8088}
.quote-badge{position:absolute;left:126px;top:231px;width:68px;height:34px;border-radius:34px 34px 0 0;background:var(--blue);color:#fff;font-size:34px;font-weight:700;line-height:50px}
.review-name{margin-top:36px;font-size:17px;font-weight:600;color:#333}
.review-city{margin-top:6px;font-size:13px;color:#8a8f96}

/* why choose */
.why{top:3300px;height:604px;background:
  radial-gradient(ellipse 380px 220px at 880px 300px,rgba(240,232,214,.9),transparent 70%),
  linear-gradient(180deg,#8fb2c4 0%,#c7c9be 45%,#6c7c6a 72%,#2f78ae 100%)}
.why-panel{top:65px;left:93px;width:491px;height:466px;background:#fff;border-radius:6px;padding:55px 50px 0 50px}
.why-panel h2{margin-top:8px;font-size:32px;font-weight:600;color:var(--navy)}
.why-item{display:flex;gap:18px;margin-top:26px}
.why-item:first-of-type{margin-top:22px}
.why-item h4{font-size:12px;font-weight:700;color:var(--navy)}
.why-item p{margin-top:4px;font-size:13px;line-height:26px;color:var(--text);width:340px}

/* contact */
.contact{top:3904px;height:791px;background:var(--grey-bg)}
.form-card{top:213px;left:140px;width:912px;height:474px;background:#fff;border-radius:6px;box-shadow:0 4px 18px rgba(0,0,0,.05)}
.field{position:absolute;width:391px;height:40px;border:2px solid #2f7fc9;border-radius:20px;padding:0 34px;display:flex;align-items:center;font-size:12px;font-style:italic;color:#666}
.field label{position:absolute;top:-9px;left:30px;padding:0 5px;background:#fff;font-size:12px;font-style:normal;font-weight:600;color:var(--navy)}
.field.active{background:#dceefa;border-color:#8fc4ec}
.field.active label{background:transparent;color:var(--blue);top:-2px}
.field.active span{margin-top:14px}
.field.message{width:802px;height:148px;border-radius:14px;align-items:flex-start;padding-top:18px}
.form-social{top:412px;left:67px;display:flex;gap:10px}
.form-social span{width:28px;height:28px;border-radius:50%;border:1.5px solid #3a8ad6}
.btn-submit{top:391px;left:703px;width:144px;height:40px;border-radius:20px;background:var(--blue);color:#fff;font-size:12px;font-weight:700;display:flex;align-items:center;justify-content:center;gap:14px}
.btn-submit i{width:24px;height:24px;border-radius:50%;background:#fff;display:flex;align-items:center;justify-content:center}

/* footer */
.site-footer{top:4695px;height:525px;background:var(--navy-deep);color:#fff}
.foot-social{top:63px;left:87px;display:flex;gap:8px}
.foot-social span{width:40px;height:40px;border-radius:2px;background:#2b4d8e}
.foot-social span:nth-child(2){background:#1f6aa0}
.foot-social span:nth-child(3){background:#2a8bd6}
.foot-social span:nth-child(4){background:#c91a28}
.foot-brand{top:66px;left:400px;width:400px;text-align:center;font-size:22px;font-weight:600;letter-spacing:2px;color:#4aa6ee;text-transform:uppercase}
.back-top{top:63px;left:972px;display:flex;align-items:center;gap:14px;font-size:13px;font-weight:700}
.back-top i{width:44px;height:44px;border-radius:2px;background:var(--blue);display:flex;align-items:center;justify-content:center}
.foot-title{top:200px;font-size:26px;font-weight:600}
.foot-copy{top:247px;left:300px;width:600px;text-align:center;font-size:14px;line-height:26px;color:#e6e9f2}
.foot-contact{top:336px;display:flex;align-items:center;gap:14px}
.foot-contact small{display:block;font-size:14px;color:#cfd5e4}
.foot-contact strong{display:block;font-size:14px;font-weight:700}
.foot-bar{top:466px;height:59px;left:0;width:1200px;background:var(--navy-bar);font-size:13px;display:flex;align-items:center;padding:0 85px}
.foot-bar nav{margin-left:auto;display:flex;gap:24px}
</style>
</head>
<body>

<header class="site-header">
  <div class="abs contact-chip" style="left:124px">
    <div class="chip-icon"><svg width="14" height="14" viewBox="0 0 24 24"><path fill="#fff" d="M6.6 10.8a15.2 15.2 0 0 0 6.6 6.6l2.2-2.2c.3-.3.7-.4 1-.2 1.1.4 2.3.6 3.6.6.6 0 1 .4 1 1V20c0 .6-.4 1-1 1A17 17 0 0 1 3 4c0-.6.4-1 1-1h3.5c.6 0 1 .4 1 1 0 1.3.2 2.5.6 3.6.1.3 0 .7-.2 1z"/></svg></div>
    <div class="chip-text"><b>Call Us:</b>(209) 555-0148</div>
  </div>
  <div class="abs contact-chip" style="left:281px">
    <div class="chip-icon"><svg width="14" height="12" viewBox="0 0 24 18"><rect x="1" y="1" width="22" height="16" rx="2" fill="none" stroke="#fff" stroke-width="2"/><path d="M2 2l10 8 10-8" fill="none" stroke="#fff" stroke-width="2"/></svg></div>
    <div class="chip-text"><b>Email:</b>office@marlowpool.example</div>
  </div>
  <div class="abs book-btn">BOOK APPOINTMENT</div>
  <div class="abs header-rule" style="left:122px;width:362px"></div>
  <div class="abs header-rule" style="left:706px;width:358px"></div>
  <nav class="main-nav">
    <a style="left:126px">Home</a>
    <a style="left:237px">About Us</a>
    <a style="left:389px">Services</a>
    <a style="left:707px">Gallery</a>
    <a style="left:845px">Our Team</a>
    <a style="left:969px">Contact Us</a>
  </nav>
</header>

<section class="hero" role="img" aria-label="Woman relaxing beside a swimming pool at sunset">
  <p class="abs hero-kicker">Crafting Memories,</p>
  <h1 class="abs hero-title">One Pool at a Time</h1>
  <div class="abs hero-rule"></div>
  <p class="abs hero-copy">Lorem ipsum dolor sit amet, consectetur adipiscing elit, sed do eiusmod tempor ididunt ut labore et dolore magna aliqua</p>
  <a class="abs btn btn-learn">LEARN MORE</a>
  <a class="abs btn btn-quote">REQUEST QUOTE</a>
</section>

<div class="abs logo-tab" style="z-index:4"><span class="brand">Marlow Pool Service</span></div>

<div class="abs features">
  <article class="feature">
    <div class="feature-icon"><svg width="34" height="34" viewBox="0 0 24 24" fill="none" stroke="#2c8ee6" stroke-width="1.4"><circle cx="12" cy="12" r="3.2"/><path d="M12 2.5l1.6 2.3 2.7-.7.7 2.7 2.7.7-.7 2.7L21.5 12l-2.3 1.6.7 2.7-2.7.7-.7 2.7-2.7-.7L12 21.5l-1.6-2.3-2.7.7-.7-2.7-2.7-.7.7-2.7L2.5 12l2.3-1.6-.7-2.7 2.7-.7.7-2.7 2.7.7z"/></svg></div>
    <h3>Expertise</h3>
    <p>Lorem ipsum dolor sit amet, consect adipiscing elit, sed do eiusmod tempor incididunt ut labore et dolore</p>
  </article>
  <article class="feature">
    <div class="feature-icon"><svg width="34" height="34" viewBox="0 0 24 24" fill="none" stroke="#2c8ee6" stroke-width="1.4"><circle cx="11" cy="11" r="8"/><path d="M3 11h16M11 3c2.5 2.5 2.5 13.5 0 16M11 3c-2.5 2.5-2.5 13.5 0 16"/><circle cx="18" cy="18" r="3" fill="#fff"/></svg></div>
    <h3>Professional</h3>
    <p>Lorem ipsum dolor sit amet, consect adipiscing elit, sed do eiusmod tempor incididunt ut labore et dolore</p>
  </article>
  <article class="feature">
    <div class="feature-icon"><svg width="34" height="34" viewBox="0 0 24 24" fill="none" stroke="#2c8ee6" stroke-width="1.4"><circle cx="12" cy="8" r="4"/><path d="M4 21c0-4.4 3.6-7 8-7s8 2.6 8 7z"/></svg></div>
    <h3>Experienced</h3>
    <p>Lorem ipsum dolor sit amet, consect adipiscing elit, sed do eiusmod tempor incididunt ut labore et dolore</p>
  </article>
</div>

<p class="abs eyebrow" style="top:1181px;left:97px">See the difference</p>
<h2 class="abs about-title">Inspired Designs,<br>Impeccable Craftsmanship</h2>
<p class="abs about-copy">Lorem ipsum dolor sit amet, consectetur adipiscing elit, sed do eius mod tempor incididunt ut labore et dolore magna aliqua. Ut enim ad minim veniam, quis nostrud exercitation ullamco laboris nisi ut aliquip ex ea commodo consequat. Duis aute irure dolor in Lorem ipsum dolor sit amet, consectetur adipiscing elit, sed do eius mod tempor incididunt ut labore et dolore magna aliqua. Ut enim ad minim veniam, quis nostrud exercitation ullamco laboris nisi ut aliquip ex ea commodo consequat. Duis aute irure dolor in</p>
<a class="abs btn-contact">Contact us <svg width="18" height="12" viewBox="0 0 18 12" fill="none" stroke="#fff" stroke-width="1.6"><path d="M0 6h16M11 1l5 5-5 5"/></svg></a>
<div class="abs about-ring"></div>
<div class="abs about-photo" role="img" aria-label="Technician in a red cap servicing pool equipment on the pool deck"></div>
<div class="abs about-dot"><svg width="20" height="20" viewBox="0 0 20 20"><circle cx="10" cy="10" r="5" fill="none" stroke="#2c8ee6" stroke-width="1.6"/></svg></div>

<section class="services">
  <p class="abs eyebrow center centered" style="top:60px">Our Services</p>
  <h2 class="abs section-title centered" style="top:82px">Services We Offer</h2>
  <p class="abs section-lead" style="top:144px">Lorem ipsum dolor sit amet, consectetur adipiscing elit, sed do eiusmod tempor incididunt ut labore et dolore magna aliqua. Ut enim ad minim veniam, quis nostrud exercitation</p>
  <div class="abs service-row">
    <div class="service">
      <div class="service-photo" role="img" aria-label="Worker repairing blue pool tiles" style="background:linear-gradient(135deg,#5f9ec7,#9dc7e0 55%,#3f7fae)"></div>
      <div class="service-label">Pool Repair</div>
    </div>
    <div class="service">
      <div class="service-photo" role="img" aria-label="Construction crew in hard hats and safety vests" style="background:linear-gradient(135deg,#c9d3dc,#8e9aa6 50%,#4a5a6b)"></div>
      <div class="service-label">Pool Construction</div>
    </div>
    <div class="service">
      <div class="service-photo" role="img" aria-label="Family enjoying a clean backyard pool" style="background:linear-gradient(180deg,#6f9a62 0%,#4fb6d8 45%,#5cc3e0 75%,#a07a55 100%)"></div>
      <div class="service-label">Pool Cleaning</div>
    </div>
  </div>
</section>

<section class="call-band" role="img" aria-label="Modern house with pool at dusk">
  <h2 class="abs call-title centered">We're On <span>Call 24/7</span> to React Promptly to Your<br>Swimming Pool Needs</h2>
</section>
<div class="abs call-bar"><span style="margin-left:28px">+ (001) 555-014-2290</span><span style="margin-left:32px">[or]</span><span style="margin-left:32px">hello@marlowpool.example</span></div>

<section class="testimonials">
  <p class="abs eyebrow center centered" style="top:58px">Testimonials</p>
  <h2 class="abs section-title centered" style="top:80px">What Clients are Saying</h2>
  <p class="abs section-lead" style="top:142px">Lorem ipsum dolor sit amet, consectetur adipiscing elit, sed do eiusmod tempor incididunt ut labore et dolore magna aliqua. Ut enim ad minim veniam, quis nostrud exercitation</p>
  <div class="abs review-row">
    <article class="review">
      <div class="review-card"><div class="stars">★★★★★</div><p>Lorem ipsum dolor sit amet, consectetur adipiscing elit, sed do eiusmod tempor incididunt ut labore et dolore</p></div>
      <div class="avatar" role="img" aria-label="Client portrait"></div>
      <div class="quote-badge">“</div>
      <p class="review-name">Owen Hartley</p><p class="review-city">Los Angeles</p>
    </article>
    <article class="review">
      <div class="review-card"><div class="stars">★★★★★</div><p>Lorem ipsum dolor sit amet, consectetur adipiscing elit, sed do eiusmod tempor incididunt ut labore et dolore</p></div>
      <div class="avatar" role="img" aria-label="Client portrait"></div>
      <div class="quote-badge">“</div>
      <p class="review-name">Owen Hartley</p><p class="review-city">Los Angeles</p>
    </article>
    <article class="review">
      <div class="review-card"><div class="stars">★★★★★</div><p>Lorem ipsum dolor sit amet, consectetur adipiscing elit, sed do eiusmod tempor incididunt ut labore et dolore</p></div>
      <div class="avatar" role="img" aria-label="Client portrait"></div>
      <div class="quote-badge">“</div>
      <p class="review-name">Owen Hartley</p><p class="review-city">Los Angeles</p>
    </article>
  </div>
</section>

<section class="why" role="img" aria-label="White villa with a pool and palm trees">
  <div class="abs why-panel">
    <p class="eyebrow">See the difference</p>
    <h2>Why Choose Us?</h2>
    <div class="why-item">
      <svg width="36" height="36" viewBox="0 0 24 24" fill="none" stroke="#2c8ee6" stroke-width="1.3"><path d="M4 15a8 8 0 1 1 16 0"/><path d="M12 15l3-5"/><circle cx="12" cy="15" r="1.3"/><path d="M7 20h10"/></svg>
      <div><h4>Quality Assurance</h4><p>Lorem ipsum dolor sit amet, consectetur adipiscing elit, sed do eiusmod tempor incididunt ut labore et</p></div>
    </div>
    <div class="why-item">
      <svg width="36" height="36" viewBox="0 0 24 24" fill="none" stroke="#2c8ee6" stroke-width="1.3"><path d="M12 3l2.6 5.4 5.9.8-4.3 4.1 1 5.8L12 16.3 6.8 19.1l1-5.8L3.5 9.2l5.9-.8z"/></svg>
      <div><h4>Proven Record</h4><p>Lorem ipsum dolor sit amet, consectetur adipiscing elit, sed do eiusmod tempor incididunt ut labore et</p></div>
    </div>
    <div class="why-item">
      <svg width="36" height="36" viewBox="0 0 24 24" fill="none" stroke="#2c8ee6" stroke-width="1.3"><circle cx="10" cy="7" r="3"/><path d="M4 20c0-4 2.7-6.5 6-6.5M14 13l6 6M13 21h8"/></svg>
      <div><h4>Comprehensive Services</h4><p>Lorem ipsum dolor sit amet, consectetur adipiscing elit, sed do eiusmod tempor incididunt ut labore et</p></div>
    </div>
  </div>
</section>

<section class="contact">
  <p class="abs eyebrow center centered" style="top:46px">Contact us</p>
  <h2 class="abs section-title centered" style="top:68px">Get In Touch With Us</h2>
  <p class="abs section-lead" style="top:130px">Lorem ipsum dolor sit amet, consectetur adipiscing elit, sed do eiusmod tempor incididunt ut labore et dolore magna aliqua. Ut enim ad minim veniam, quis nostrud exercitation</p>
  <form class="abs form-card">
    <div class="field active" style="left:55px;top:61px"><label>Your Name</label><span>John</span></div>
    <div class="field" style="left:466px;top:61px"><label>Your Website</label><span>www.yoursite.example</span></div>
    <div class="field" style="left:55px;top:136px"><label>Your Phone</label><span>123 456 789</span></div>
    <div class="field" style="left:466px;top:136px"><label>Your Email</label><span>name@yourmail.example</span></div>
    <div class="field message" style="left:55px;top:213px"><label>Your Message</label><span>Type Message</span></div>
    <div class="abs form-social"><span></span><span></span><span></span><span></span></div>
    <div class="abs btn-submit">Submit Now <i><svg width="12" height="10" viewBox="0 0 12 10" fill="none" stroke="#2c9cf0" stroke-width="1.6"><path d="M0 5h10M6 1l4 4-4 4"/></svg></i></div>
  </form>
</section>

<footer class="site-footer">
  <div class="abs foot-social"><span></span><span></span><span></span><span></span></div>
  <div class="abs foot-brand">Marlow Pool Service</div>
  <div class="abs back-top">Back to top <i><svg width="16" height="10" viewBox="0 0 16 10" fill="none" stroke="#fff" stroke-width="2"><path d="M1 9l7-7 7 7"/></svg></i></div>
  <h2 class="abs foot-title centered">Get free assessment today</h2>
  <p class="abs foot-copy">Lorem ipsum dolor sit amet, consectetur adipiscing elit, sed do eiusmod tempor incididunt ut labore et dolore magna aliqua.</p>
  <div class="abs foot-contact" style="left:219px">
    <svg width="50" height="50" viewBox="0 0 24 24" fill="none" stroke="#3d8fe0" stroke-width="1"><path d="M6.6 10.8a15.2 15.2 0 0 0 6.6 6.6l2.2-2.2c.3-.3.7-.4 1-.2 1.1.4 2.3.6 3.6.6.6 0 1 .4 1 1V20c0 .6-.4 1-1 1A17 17 0 0 1 3 4c0-.6.4-1 1-1h3.5c.6 0 1 .4 1 1 0 1.3.2 2.5.6 3.6.1.3 0 .7-.2 1z"/></svg>
    <div><small>Make a Call</small><strong>+1-209-555-0177</strong></div>
  </div>
  <div class="abs foot-contact" style="left:476px">
    <svg width="50" height="50" viewBox="0 0 24 24" fill="none" stroke="#3d8fe0" stroke-width="1"><rect x="2" y="5" width="20" height="15" rx="1"/><path d="M2 6l10 8 10-8M2 20l7-6M22 20l-7-6"/></svg>
    <div><small>Mail Us On</small><strong>care@marlowpool.example</strong></div>
  </div>
  <div class="abs foot-contact" style="left:758px">
    <svg width="50" height="50" viewBox="0 0 24 24" fill="none" stroke="#3d8fe0" stroke-width="1"><path d="M12 21s-6-6.2-6-11a6 6 0 0 1 12 0c0 4.8-6 11-6 11z"/><circle cx="12" cy="10" r="2.3"/><path d="M3 21h18"/></svg>
    <div><small>Location</small><strong>418 Harbor Crest Rd</strong></div>
  </div>
  <div class="foot-bar abs">
    <span>Marlow Pool Service</span>
    <nav><span>Privacy Policy</span><span>Terms &amp; Conditions</span><span>Site Map</span></nav>
  </div>
</footer>

</body>
</html>
```